New Business Card Design Project

I need a design for business cards, i am an electrical business called "Corvane Electrical and Communications" i need the cards to be double sided with the company logo on the back (attached) the front needs to say my company name, web site, email address, telephone number, and ABN number and electrical license number. I am open to different arrangements of the information but would like the background to be incorporating something electrical or something that looks smart. open to all additional ideas also.

The company colours are orange and grey see logo attached.

Business Name: Corvane Electrical and Communications
Website: corvaneelectricalandcomms.example.com.au
Email: brent@corvaneelectricalandcomms.example.com.au
Telephone(mobile): 0481209736
ABN: 71208349162
Lic No: 418273D

Target Market(s)

Business entities, Project Managers, Accounts, Clients

Industry/Entity Type

Electrician

Contact Information for Business Card

I need a design for business cards, i am an electrical business called "Corvane Electrical and Communications" i need the cards to be double sided with the company logo on the back (attached) the front needs to say my company name

Font styles to use
Serif
Sans Serif

Colors
f37122
5c5c5c

Requirements
Must have
• Must have the Logo on the back open to different ways of it being on the back but had in mind to keep it central but again open to other options
Nice to have
• A real modern cool background that is eye catching yet contemporary
Should not have
• No backgrounds of a light bulb or plug or anything like that

```html
<!DOCTYPE html>
<html lang="en">
<head>
<meta charset="utf-8">
<title>Corvane Electrical and Communications – Business Cards</title>
<link href="https://fonts.googleapis.com/css2?family=Open+Sans:wght@400;600;700&display=swap" rel="stylesheet">
<style>
  :root {
    --amber: #f8ac1e;
    --ink: #222222;
    --grey: #5c5c5c;
    --paper: #ffffff;
    --backdrop: #e8e5e2;
  }
  * { margin: 0; padding: 0; box-sizing: border-box; }
  html, body { width: 1200px; height: 900px; overflow: hidden; }
  body {
    position: relative;
    background: var(--backdrop);
    font-family: "Open Sans", Arial, sans-serif;
    color: var(--ink);
  }
  .card {
    position: absolute;
    border-radius: 14px;
    overflow: hidden;
    box-shadow: 0 6px 18px rgba(0,0,0,0.18);
  }
  .card-front { left: 78px; top: 34px; width: 588px; height: 364px; background: var(--paper); }
  .card-back  { left: 390px; top: 506px; width: 564px; height: 349px; background: var(--amber); }
  .card-shape { position: absolute; left: 0; top: 0; }

  .wordmark {
    position: absolute;
    text-align: center;
    font-weight: 600;
    line-height: 1;
  }
  .card-front .wordmark { left: 140px; width: 307px; top: 44px; color: var(--ink); }
  .card-back .wordmark  { left: 106px; width: 352px; top: 100px; color: var(--paper); }
  .wordmark-name { display: block; font-size: 44px; letter-spacing: 3px; }
  .wordmark-tag  { display: block; font-size: 11.5px; letter-spacing: 1.2px; margin-top: 10px; }
  .card-back .wordmark-name { font-size: 50px; }
  .card-back .wordmark-tag  { font-size: 12.5px; }

  .holder { position: absolute; left: 43px; top: 208px; }
  .holder-name { font-size: 20px; font-weight: 600; color: var(--amber); line-height: 1.1; }
  .holder-role { font-size: 14px; color: var(--ink); margin-top: 3px; }

  .credentials { position: absolute; left: 43px; top: 272px; font-size: 14px; line-height: 25px; }
  .credentials dt { display: inline; font-weight: 700; font-size: 15px; }
  .credentials dd { display: inline; font-weight: 600; }
  .credentials div { white-space: nowrap; }

  .contacts {
    position: absolute; right: 36px; top: 249px;
    list-style: none; text-align: right;
    font-size: 13.5px; line-height: 25px;
  }
  .contacts li { display: flex; justify-content: flex-end; align-items: center; gap: 8px; white-space: nowrap; }
  .contacts li.email { font-size: 12.8px; }
  .contacts svg { width: 12px; height: 12px; flex: none; }

  .back-web {
    position: absolute; left: 0; width: 100%; top: 286px;
    text-align: center; color: var(--paper);
    font-size: 16px; font-weight: 600;
  }
</style>
</head>
<body>

<section class="card card-front" aria-label="Business card front">
  <svg class="card-shape" width="588" height="364" viewBox="0 0 588 364" aria-hidden="true">
    <rect x="0" y="30" width="588" height="98" fill="var(--amber)"/>
    <rect x="140" y="14" width="307" height="128" rx="64" fill="var(--paper)"/>
  </svg>
  <div class="wordmark">
    <span class="wordmark-name">CORVANE</span>
    <span class="wordmark-tag">ELECTRICAL &amp; COMMUNICATIONS</span>
  </div>

  <div class="holder">
    <p class="holder-name">Dana Whitfield</p>
    <p class="holder-role">Director</p>
  </div>

  <dl class="credentials">
    <div><dt>ABN:</dt> <dd>71208349162</dd></div>
    <div><dt>Lic No:</dt> <dd>418273D</dd></div>
  </dl>

  <ul class="contacts">
    <li class="phone">0481209736
      <svg viewBox="0 0 12 12" aria-hidden="true"><path d="M2.5 1 L4.5 1 L5.3 3.4 L4 4.4 C4.6 5.8 6.2 7.4 7.6 8 L8.6 6.7 L11 7.5 L11 9.5 C11 10.4 10.4 11 9.5 11 C5 11 1 7 1 2.5 C1 1.6 1.6 1 2.5 1 Z" fill="var(--amber)"/></svg>
    </li>
    <li class="email">brent@corvaneelectricalandcomms.example.com.au
      <svg viewBox="0 0 12 12" aria-hidden="true"><rect x="0.5" y="2.5" width="11" height="7.5" fill="var(--amber)"/><path d="M0.8 2.8 L6 6.8 L11.2 2.8" stroke="var(--paper)" stroke-width="1" fill="none"/></svg>
    </li>
    <li class="web">corvaneelectricalandcomms.example.com.au
      <svg viewBox="0 0 12 12" aria-hidden="true"><circle cx="6" cy="6" r="5.5" fill="var(--amber)"/><path d="M0.5 6 H11.5 M6 0.5 C3.5 3 3.5 9 6 11.5 M6 0.5 C8.5 3 8.5 9 6 11.5" stroke="var(--paper)" stroke-width="0.8" fill="none"/></svg>
    </li>
  </ul>
</section>

<section class="card card-back" aria-label="Business card back">
  <svg class="card-shape" width="564" height="349" viewBox="0 0 564 349" aria-hidden="true">
    <rect x="0" y="81" width="564" height="96" fill="var(--paper)"/>
    <rect x="106" y="66" width="352" height="126" rx="63" fill="var(--amber)"/>
  </svg>
  <div class="wordmark">
    <span class="wordmark-name">CORVANE</span>
    <span class="wordmark-tag">ELECTRICAL &amp; COMMUNICATIONS</span>
  </div>
  <p class="back-web">corvaneelectricalandcomms.example.com.au</p>
</section>

</body>
</html>
```